Powerpoint, Graphics for Sermon Series

I am starting a sermon series on the short letters if Scripture that are between Hebrews and Revelation. The sermon series will be called "Walking Unmarked Trails: Lasting Lessons from Quiet Hills."

Think about finding a packet of letters in an Attic. There is only the dialogue of the writer. We don't know exactly what the receivers were going through or even what their response to the letters were/are!

Target Market(s)

Local Church

Industry/Entity Type

Christian

Font styles to use
Serif
Sans Serif

Colors

Designer to choose colors to be used in the design.

Requirements
Must have
• Powerpoint Slide with Title -
• Background Slide -
• It would be great to have both JPG, PNG, and Photoshop/Indesign that can be used for powerpoint, both in 4x3 ration and wide... Need Title Slide with typography and background slide for text to go over the top of.
• Stick with the theme -- Walking Unmarked Trails
• I am including our church logo, but don't feel like you need to use it in anyway.
Nice to have
• Social Media Slides - Square Slide, Facebook Header
• Greyscale Version?

```html
<!DOCTYPE html>
<html lang="en">
<head>
<meta charset="UTF-8">
<title>Walking Unmarked Trails – Content Slide</title>
<link href="https://fonts.googleapis.com/css2?family=Cinzel:wght@700&family=Lato:wght@400;700&display=swap" rel="stylesheet">
<style>
  :root {
    --title-brown: #6a3c1c;
    --accent-amber: #c77a0e;
    --body-ink: #454545;
    --header-paper: rgba(244, 242, 239, 0.95);
    --panel-paper: rgba(248, 247, 246, 0.94);
    --wood-dark: #3b2318;
    --wood-mid: #6a4030;
    --wood-warm: #8c5c42;
    --letter-tan: #c8a06a;
    --letter-shade: #9c7448;
    --sheet-cream: #e6dccb;
    --sun-spot: #d9a57a;
  }
  html, body {
    margin: 0;
    padding: 0;
    width: 1200px;
    height: 900px;
    overflow: hidden;
    background: #ffffff;
  }
  .slide {
    position: relative;
    width: 1200px;
    height: 900px;
    overflow: hidden;
    font-family: "Lato", sans-serif;
  }
  .hero-photo {
    position: absolute;
    left: 0;
    top: 0;
    width: 1200px;
    height: 900px;
    background:
      radial-gradient(ellipse 300px 250px at 390px 500px, var(--letter-tan) 0%, rgba(200,160,106,0.9) 45%, rgba(156,116,72,0.55) 75%, rgba(156,116,72,0) 100%),
      radial-gradient(ellipse 420px 300px at 640px 420px, var(--sheet-cream) 0%, rgba(230,220,203,0.8) 50%, rgba(230,220,203,0) 100%),
      radial-gradient(ellipse 260px 90px at 520px 820px, rgba(217,165,122,0.7) 0%, rgba(217,165,122,0) 100%),
      radial-gradient(ellipse 200px 80px at 1020px 860px, rgba(217,165,122,0.5) 0%, rgba(217,165,122,0) 100%),
      radial-gradient(ellipse 220px 120px at 150px 760px, rgba(180,120,90,0.55) 0%, rgba(180,120,90,0) 100%),
      linear-gradient(170deg, var(--wood-warm) 0%, var(--wood-mid) 40%, #5a3526 70%, var(--wood-dark) 100%);
  }
  .slide-header {
    position: absolute;
    left: 0;
    top: 0;
    width: 1200px;
    height: 140px;
    background: var(--header-paper);
  }
  .slide-title {
    position: absolute;
    left: 43px;
    top: 32px;
    margin: 0;
    font-family: "Cinzel", serif;
    font-weight: 700;
    font-size: 47px;
    letter-spacing: 0.3px;
    color: var(--title-brown);
    line-height: 1.2;
  }
  .church-name {
    position: absolute;
    right: 26px;
    top: 46px;
    display: flex;
    align-items: center;
    gap: 12px;
    font-family: "Lato", sans-serif;
    font-weight: 700;
    font-size: 30px;
    color: var(--title-brown);
  }
  .church-name .mark {
    width: 18px;
    height: 18px;
    background: var(--title-brown);
  }
  .text-panel {
    position: absolute;
    left: 714px;
    top: 252px;
    width: 486px;
    height: 536px;
    box-sizing: border-box;
    padding: 36px 24px 0 35px;
    background: var(--panel-paper);
  }
  .panel-heading {
    margin: 0 0 2px 0;
    font-family: "Lato", sans-serif;
    font-weight: 700;
    font-size: 33px;
    line-height: 1.2;
    color: var(--accent-amber);
  }
  .panel-body {
    margin: 0;
    font-family: "Lato", sans-serif;
    font-weight: 400;
    font-size: 22.4px;
    line-height: 37.5px;
    color: var(--body-ink);
  }
</style>
</head>
<body>
  <div class="slide">
    <div class="hero-photo" role="img" aria-label="Bundle of old handwritten letters with an antique iron key resting on a sunlit wooden table"></div>

    <header class="slide-header">
      <h1 class="slide-title">SLIDE TITLE HERE</h1>
      <div class="church-name"><span class="mark"></span>Cedar Ridge Fellowship</div>
    </header>

    <section class="text-panel">
      <h2 class="panel-heading">Subtext title here</h2>
      <p class="panel-body">Lorem Ipsum is simply dummy text of the printing and typesetting industry. Lorem Ipsum has been the industry's standard dummy text ever since the 1500s, when an unknown printer took a galley of type and scrambled it to make a type specimen book. It has survived not only five centu&shy;ries, but also the leap into electronic type&shy;setting, remaining essentially unchanged. It was popularised in the 1960s with the release .</p>
    </section>
  </div>
</body>
</html>
```